Seeking for catalogue design -for Event Mgmt company

Need to be creative and striking and images to be more enhanced.
The items in the catalogue have to be layout well and easy to read.
Cover and background of catalogue needs to be striking but not overpowering the items.
Catologue needs to be able to put up on website and able to read on mobile.
Font used must be easily readable and not too small.

Target Market(s)

Business and Public Sectors

Industry/Entity Type

Event Planning

Colors

Designer to choose colors to be used in the design.

Requirements
Must have
• Not too many colors but must be creative
Nice to have
• See that the images of items in catalogue have better layout
Should not have
• Not to be so messy

```html
<!DOCTYPE html>
<html lang="en">
<head>
<meta charset="utf-8">
<title>Marlowe Events – Fun Fair &amp; Carnival Catalogue</title>
<link href="https://fonts.googleapis.com/css2?family=Arimo:wght@400;700&display=swap" rel="stylesheet">
<style>
  :root {
    --paper: #ffffff;
    --teal-deep: #5fc4c4;
    --teal-mid: #8fd6d4;
    --teal-soft: #c4ebe8;
    --teal-mist: #e3f5f3;
    --ink: #2a2a2a;
    --heading: #333333;
    --frame: #8a8a8a;
    --logo-box: #8d8d8d;
    --footer-band: #c9d3da;
    --footer-ink: #1f3550;
  }
  * { margin: 0; padding: 0; box-sizing: border-box; }
  html, body { width: 848px; height: 1200px; overflow: hidden; background: var(--paper); }
  body { font-family: "Arimo", Arial, sans-serif; color: var(--ink); }
  .catalogue { position: relative; width: 848px; height: 1200px; overflow: hidden; background: var(--paper); }
  .backdrop { position: absolute; inset: 0; }

  .brand {
    position: absolute; left: 4px; top: 4px; width: 194px; height: 62px;
    background: var(--logo-box); color: #fff;
    box-shadow: 3px 3px 5px rgba(0,0,0,.35);
    display: flex; flex-direction: column; justify-content: center; padding-left: 12px;
  }
  .brand-name { font-size: 26px; font-weight: 700; letter-spacing: .5px; line-height: 1; }
  .brand-sub { font-size: 8px; font-weight: 700; letter-spacing: .4px; margin-top: 5px; }

  .item { position: absolute; width: 270px; text-align: center; }
  .item-category { font-size: 15px; font-weight: 700; color: var(--heading); letter-spacing: .2px; height: 20px; }
  .item-photo {
    display: block; margin: 4px auto 0; width: 170px; height: 172px;
    border: 5px solid var(--frame); box-shadow: 2px 3px 6px rgba(0,0,0,.35);
  }
  .item-details { margin-top: 30px; font-size: 13.5px; line-height: 1.22; color: var(--ink); }

  .col-1 { left: 3px; } .col-2 { left: 300px; } .col-3 { left: 594px; }
  .row-1 { top: 114px; } .row-2 { top: 468px; } .row-3 { top: 820px; }

  .photo-bowling { background: linear-gradient(160deg, #f1e4d6, #d9b48a 55%, #c9935e); }
  .photo-basket { background: linear-gradient(180deg, #f5e9e9, #d62a2a 45%, #e9c23a); }
  .photo-balloon { background: linear-gradient(170deg, #d8332e, #2e3a7a 50%, #e8e0e0); }
  .photo-ringtoss { background: linear-gradient(170deg, #f2ecd9, #f0e6b6 50%, #c7c37b); }
  .photo-tent { background: linear-gradient(180deg, #4a4a44, #cf3a3a 40%, #e8e6e2 60%, #5c5a52); }
  .photo-panel { background: linear-gradient(180deg, #8a2a2a, #c93a3a 55%, #b08a5a); }
  .photo-sound { background: linear-gradient(160deg, #2c3b4a, #6a7580 50%, #1f262d); }
  .photo-tubes { background: linear-gradient(180deg, #e8eef0, #e04848 40%, #3fa56a 70%, #6a7d5a); }
  .photo-ballpit { background: linear-gradient(160deg, #2a6fb8, #e8c23a 45%, #d83a3a 70%, #3a9a4a); }

  .notes {
    position: absolute; left: 0; top: 1128px; width: 848px; height: 72px;
    background: var(--footer-band); padding: 6px 12px;
    font-size: 13.4px; font-weight: 700; color: var(--footer-ink); line-height: 1.32;
  }
</style>
</head>
<body>
<main class="catalogue">
  <svg class="backdrop" width="848" height="1200" viewBox="0 0 848 1200" aria-hidden="true">
    <circle cx="430" cy="760" r="560" fill="var(--teal-mist)"/>
    <circle cx="-60" cy="900" r="520" fill="var(--teal-soft)" opacity=".7"/>
    <circle cx="560" cy="640" r="330" fill="var(--paper)" opacity=".55"/>
    <circle cx="760" cy="1160" r="300" fill="var(--teal-mid)" opacity=".35"/>
    <circle cx="780" cy="30" r="250" fill="var(--teal-soft)"/>
    <circle cx="800" cy="10" r="205" fill="var(--teal-deep)"/>
  </svg>

  <div class="brand">
    <span class="brand-name">MARLOWE</span>
    <span class="brand-sub">MARLOWE EVENTS PTE LTD</span>
  </div>

  <section class="item col-1 row-1">
    <h2 class="item-category">FUN FAIR GAMES</h2>
    <div class="item-photo photo-bowling" role="img" aria-label="Carnival bowling game lane with pins and ball"></div>
    <p class="item-details">Bowling Game<br>0.72m by 1.7m by 0.30m<br>$300/Stall<br>Require 1x long table/stall<br>$550/2 stalls</p>
  </section>

  <section class="item col-2 row-1">
    <h2 class="item-category">FUN FAIR GAMES</h2>
    <div class="item-photo photo-basket" role="img" aria-label="Red and yellow carnival basket toss game stations"></div>
    <p class="item-details">Basket Toss<br>0.64m by 0.7m by 1.37m<br>$360/Stall<br>$980/3 stalls</p>
  </section>

  <section class="item col-3 row-1">
    <h2 class="item-category">FUN FAIR GAMES</h2>
    <div class="item-photo photo-balloon" role="img" aria-label="Large balloon dart game stall with striped base"></div>
    <p class="item-details">Large Balloon Dart Game<br>1.98m by 0.6m by 2.2m<br>inclusive of 200 balloons<br>$960/game stall</p>
  </section>

  <section class="item col-1 row-2">
    <h2 class="item-category">FUN FAIR GAMES</h2>
    <div class="item-photo photo-ringtoss" role="img" aria-label="Rows of bottles for the ring toss game"></div>
    <p class="item-details">Large Bottles Ring Toss Game<br>1.8m by 1.8m by 0.9m<br>inclusive of 50 colourful rings<br>$1440/game stall</p>
  </section>

  <section class="item col-2 row-2">
    <h2 class="item-category">CARNIVAL EQUIPMENT</h2>
    <div class="item-photo photo-tent" role="img" aria-label="Red and white striped carnival tent"></div>
    <p class="item-details">Carnival Tent<br>2.5m by 2.5m<br>$280/Tent (min 3 tent)</p>
  </section>

  <section class="item col-3 row-2">
    <h2 class="item-category">CARNIVAL EQUIPMENT</h2>
    <div class="item-photo photo-panel" role="img" aria-label="Customized red carnival panels set up at an event"></div>
    <p class="item-details">Customized Panel<br>0.9m by 0.6m per piece<br>Design to be sent in PDF file<br>SGD$180/panel</p>
  </section>

  <section class="item col-1 row-3">
    <h2 class="item-category">CARNIVAL EQUIPMENT</h2>
    <div class="item-photo photo-sound" role="img" aria-label="Sound mixing console"></div>
    <p class="item-details">Sound System Rental<br>speakers, 1 mixer, 2 mic, ATA cas<br>1x Sound Technician<br>SGD$850</p>
  </section>

  <section class="item col-2 row-3">
    <h2 class="item-category">CARNIVAL EQUIPMENT</h2>
    <div class="item-photo photo-tubes" role="img" aria-label="Colourful inflatable dancing tubes outdoors"></div>
    <p class="item-details">Dancing Tube<br>5m(H)<br>various colours available<br>SGD$600 for 4 Tube</p>
  </section>

  <section class="item col-3 row-3">
    <h2 class="item-category">CARNIVAL EQUIPMENT</h2>
    <div class="item-photo photo-ballpit" role="img" aria-label="Rainbow block ball pit filled with coloured balls"></div>
    <p class="item-details">Rainbow Block Ball Pit<br>2.7m by 2.4m<br>Indoor only (2000 balls)<br>SGD$700</p>
  </section>

  <footer class="notes">
    <p>*Size stated above is estimated only.</p>
    <p>*Rates include Delivery, Set up, Dismantle and Collection of the equipments.</p>
    <p>*The more items or more days rented, we may be able to quote a much better discounted package rate</p>
  </footer>
</main>
</body>
</html>
```